Investment firm needs website redesign

we want to change our site with a trendy new design. We are an investment trading firm dealing in currencies etc for retail clients. We are looking for new ideas for our website design which shows class and international reach. We want the inner pages also to be designed especially the look. We do not want the typical designs used by most sites and are looking for something new and interesting. you can review our current site www.trovanique-exchange.com.

Target Market(s)

international

Industry/Entity Type

Forex

Coding

Coded - Design and coding required

Number of Pages Required

5+ page

Font styles to use
Sans Serif

Colors

Designer to choose colors to be used in the design.

Requirements
Must have
• responsive, easy to load
Nice to have
• something trendy yet sophisticated. technology is an important part of our business
Should not have
• do not want the typical designs used by most websites

```html
<!DOCTYPE html>
<html lang="en">
<head>
<meta charset="utf-8">
<title>Vantoris Financial Markets</title>
<link href="https://fonts.googleapis.com/css2?family=Roboto:wght@300;400;500;700&display=swap" rel="stylesheet">
<style>
:root{
  --navy:#2d3269;
  --navy-deep:#1f2350;
  --night:#1c2048;
  --gold:#f4b41a;
  --gold-deep:#ee9c17;
  --slate:#2f4257;
  --grey-bg:#e9eaee;
  --text:#444a5c;
  --white:#ffffff;
  --line:#c9ccd6;
}
*{box-sizing:border-box;margin:0;padding:0}
html,body{width:1200px;height:3082px;overflow:hidden}
body{position:relative;font-family:'Roboto',sans-serif;background:var(--white);color:var(--text)}
.abs{position:absolute}

/* ticker */
.ticker{left:0;top:0;width:1200px;height:37px;background:var(--gold);display:flex;justify-content:center;align-items:center;gap:22px;font-size:12.5px;font-weight:700;color:var(--navy-deep)}
.ticker span.up::after{content:" ▲";font-size:9px}
.ticker span.down::after{content:" ▼";font-size:9px}

/* hero */
.hero{left:0;top:37px;width:1200px;height:640px;background:linear-gradient(180deg,#3a3f7a 0%,#2c3068 45%,#1d2050 100%);clip-path:polygon(0 0,100% 0,100% 90%,74% 97%,50% 100%,26% 97%,0 90%)}
.logo{left:119px;top:55px;display:flex;align-items:center;gap:12px;color:var(--white)}
.logo .mark{width:56px;height:56px;border-radius:50%;border:3px solid var(--white)}
.logo .name{font-size:30px;font-weight:500;line-height:1;letter-spacing:.5px}
.logo .sub{font-size:11px;letter-spacing:2px;display:block;margin-top:3px}
.nav{left:385px;top:72px;display:flex;color:var(--white);font-size:12.5px;font-weight:500;line-height:1.35}
.nav a{color:inherit;text-decoration:none;padding:0 22px;border-left:1px solid rgba(255,255,255,.35)}
.nav a:first-child{border-left:none;padding-left:0}
.hero-title{left:0;top:162px;width:1200px;text-align:center;color:var(--white)}
.hero-title h1{font-size:42px;font-weight:500;letter-spacing:.5px}
.hero-title p{font-size:30px;font-weight:300;margin-top:2px}
.arrow{top:325px}
.monitor{left:318px;top:290px;width:576px;height:388px;background:#1b1b1f;border-radius:10px 10px 0 0;padding:20px 26px 40px}
.monitor .screen{width:100%;height:100%;background:linear-gradient(180deg,#f4f4f6,#dfe1e6)}
.stand{left:318px;top:660px;width:576px;height:94px;background:linear-gradient(180deg,#c9cbd1,#9ea1aa);clip-path:polygon(0 0,100% 0,100% 30%,50% 100%,0 30%)}

/* feature circles */
.feature{width:310px;height:310px;border-radius:50%;color:var(--white);text-align:center;padding:60px 40px 0}
.feature h3{font-size:20px;font-weight:500;line-height:1.3;margin-top:18px}
.feature p{font-size:12px;line-height:1.6;opacity:.85;margin-top:10px}
.feature .toggle{margin:14px auto 0}
.f-navy{left:118px;top:780px;background:var(--navy)}
.f-gold{left:437px;top:780px;background:var(--gold)}
.f-slate{left:770px;top:780px;background:var(--slate)}

/* funding */
.funding{left:0;top:1161px;width:1200px;height:504px;background:var(--navy);clip-path:polygon(0 9%,100% 0,100% 100%,0 92%)}
.funding-photo{left:596px;top:1161px;width:604px;height:504px;background:linear-gradient(135deg,#b9a68c 0%,#8a7560 45%,#d9d1c5 100%);clip-path:polygon(18% 0,100% 0,100% 100%,0 100%)}
.funding-copy{left:134px;top:1298px;width:450px;color:var(--white)}
.funding-copy h2{font-size:27px;font-weight:500}
.funding-copy p{font-size:16px;line-height:1.6;margin-top:18px;opacity:.9}
.btn-ghost{display:inline-block;margin-top:34px;width:145px;height:38px;line-height:36px;border:2px solid var(--white);text-align:center;font-size:12px;font-weight:500;color:var(--white)}

/* partner & demo */
.services{left:0;top:1623px;width:1200px;height:450px;background:linear-gradient(180deg,#f3f4f6,var(--grey-bg))}
.card{top:1730px;width:473px;height:274px;background:var(--white);border:1px solid #d6d8de;box-shadow:0 2px 6px rgba(0,0,0,.08);padding:42px 30px 0 130px}
.card .ico{position:absolute;left:34px;top:44px}
.card h3{font-size:22px;font-weight:500;color:var(--navy)}
.card p{font-size:13px;line-height:1.65;margin-top:12px;color:var(--text)}
.btn-outline{display:inline-block;margin-top:16px;width:145px;height:38px;line-height:34px;border:2px solid var(--navy);text-align:center;font-size:12px;font-weight:500;color:var(--navy)}
.card-partner{left:117px}
.card-demo{left:610px}

/* callback */
.callback{left:0;top:2034px;width:1200px;height:473px;background:linear-gradient(90deg,var(--gold) 0%,var(--gold-deep) 100%);clip-path:polygon(0 5%,100% 0,100% 92%,0 100%)}
.callback h2{position:absolute;left:0;top:96px;width:1200px;text-align:center;font-size:28px;font-weight:500;color:var(--white)}
.field{position:absolute;width:402px}
.field label{display:block;font-size:14px;font-weight:700;color:var(--navy-deep);margin-bottom:8px}
.field .input{height:41px;background:var(--white)}
.btn-send{position:absolute;left:201px;top:348px;width:148px;height:39px;background:var(--navy);color:var(--white);font-size:15px;font-weight:500;text-align:center;line-height:39px}

/* partner badges */
.brands{left:0;top:2528px;width:1200px;height:104px}
.brand{position:absolute;top:34px;display:flex;align-items:center;gap:8px;font-size:18px;font-weight:500;color:#333;white-space:nowrap}
.brand .dot{width:34px;height:34px;border-radius:50%;background:var(--navy)}
.brand .sq{width:22px;height:22px;background:#555}

/* footer */
.footer{left:0;top:2651px;width:1200px;height:369px;background:linear-gradient(180deg,#262a5c,var(--night));clip-path:polygon(0 0,100% 7%,100% 100%,0 100%)}
.fcol{position:absolute;top:104px;color:var(--white)}
.fcol h4{font-size:20px;font-weight:400;margin-bottom:14px}
.fcol li{list-style:none;font-size:13px;line-height:31.5px;opacity:.9}
.social{display:flex;gap:8px;margin-top:4px}
.social span{width:32px;height:32px;border:2px solid var(--white);border-radius:50%}
.bottom-bar{left:0;top:3020px;width:1200px;height:62px;background:#161939;color:rgba(255,255,255,.6);font-size:13px;text-align:center;line-height:62px}
</style>
</head>
<body>

<div class="abs ticker">
  <span class="down">GBP/BYR = 0</span>
  <span class="down">GBP/BZD = 2.68061</span>
  <span class="down">GBP/CAD = 1.72124</span>
  <span class="down">GBP/CHF = 1.31579</span>
  <span class="up">GBP/CLP = 842.2154</span>
  <span class="down">GBP/CHF = 1.31579</span>
  <span class="up">GBP/CLP = 842.2154</span>
</div>

<section class="abs hero" role="img" aria-label="Night city skyline behind a trading monitor"></section>

<div class="abs logo">
  <div class="mark"></div>
  <div><span class="name">VANTORIS</span><span class="sub">FINANCIAL MARKETS</span></div>
</div>

<nav class="abs nav">
  <a href="#">ABOUT<br>VANTORIS</a>
  <a href="#">PRODUCTS &amp;<br>SERVICES</a>
  <a href="#">OPEN<br>ACCOUNT</a>
  <a href="#">TRADING<br>PLATFORMS</a>
  <a href="#">TRADING<br>INFO</a>
  <a href="#">PARTNER<br>PROGRAME</a>
</nav>

<div class="abs hero-title">
  <h1>TRADING CRYPTO CURRENCY PLATFORM</h1>
  <p>MORBI DIAM MAURIS VIVERRA GRAVIDA</p>
</div>

<svg class="abs arrow" style="left:96px" width="26" height="44" viewBox="0 0 26 44"><polyline points="22,3 4,22 22,41" fill="none" stroke="#fff" stroke-width="4"/></svg>
<svg class="abs arrow" style="left:1086px" width="26" height="44" viewBox="0 0 26 44"><polyline points="4,3 22,22 4,41" fill="none" stroke="#fff" stroke-width="4"/></svg>

<div class="abs stand"></div>
<div class="abs monitor"><div class="screen" role="img" aria-label="Candlestick price chart on a trading screen"></div></div>

<div class="abs feature f-navy">
  <svg width="74" height="74" viewBox="0 0 74 74" fill="none" stroke="#fff" stroke-width="2.5"><circle cx="37" cy="20" r="9"/><path d="M20 60v-14a17 17 0 0 1 34 0v14"/><circle cx="15" cy="28" r="6"/><circle cx="59" cy="28" r="6"/><path d="M4 60v-10a11 11 0 0 1 12-10M70 60v-10a11 11 0 0 0-12-10"/></svg>
  <h3>MULTI ACCOUNT<br>MANAGER</h3>
  <p>Kora Pro and Kora Trader are 2 online platforms provided...</p>
  <svg class="toggle" width="44" height="44" viewBox="0 0 44 44" fill="none" stroke="#fff" stroke-width="2"><circle cx="22" cy="22" r="20"/><polyline points="14,19 22,27 30,19"/></svg>
</div>

<div class="abs feature f-gold">
  <svg width="74" height="74" viewBox="0 0 74 74" fill="none" stroke="#fff" stroke-width="2.5"><rect x="14" y="6" width="36" height="50"/><line x1="21" y1="18" x2="43" y2="18"/><line x1="21" y1="27" x2="43" y2="27"/><line x1="21" y1="36" x2="35" y2="36"/><circle cx="52" cy="52" r="10"/><circle cx="52" cy="52" r="4"/></svg>
  <h3>CONTRACT<br>SPECIFICATIONS</h3>
  <p>The Vantoris Broker offers money managers and traders</p>
  <svg class="toggle" width="44" height="44" viewBox="0 0 44 44" fill="none" stroke="#fff" stroke-width="2"><circle cx="22" cy="22" r="20"/><polyline points="14,19 22,27 30,19"/></svg>
</div>

<div class="abs feature f-slate">
  <svg width="74" height="74" viewBox="0 0 74 74" fill="none" stroke="#fff" stroke-width="2.5"><circle cx="37" cy="37" r="33"/><circle cx="37" cy="28" r="10"/><path d="M18 60a19 19 0 0 1 38 0"/><polyline points="33,46 37,54 41,46"/></svg>
  <h3>HOW TO OPEN AN<br>ACCOUNT</h3>
  <p>Welcome to the Vantoris experience. Our account...</p>
  <svg class="toggle" width="44" height="44" viewBox="0 0 44 44" fill="none" stroke="#fff" stroke-width="2"><circle cx="22" cy="22" r="20"/><polyline points="14,19 22,27 30,19"/></svg>
</div>

<section class="abs funding"></section>
<div class="abs funding-photo" role="img" aria-label="Hands typing on a laptop showing trading charts on a wooden desk"></div>
<div class="abs funding-copy">
  <h2>FUNDING YOUR ACCOUNT</h2>
  <p>Vantoris offers easy funding for your account. With multiple payment options, you can pay from anywhere, anytime to fund your trading account. You can choose from a host of easy payment options.</p>
  <span class="btn-ghost">READ MORE</span>
</div>

<section class="abs services" role="img" aria-label="Soft grey market chart backdrop"></section>

<div class="abs card card-partner">
  <svg class="ico" width="76" height="80" viewBox="0 0 76 80" fill="none" stroke="#2d3269" stroke-width="2.5"><circle cx="38" cy="16" r="10"/><circle cx="38" cy="16" r="4"/><circle cx="38" cy="42" r="8"/><path d="M22 76v-10a16 16 0 0 1 32 0v10"/><circle cx="12" cy="50" r="6"/><circle cx="64" cy="50" r="6"/><path d="M2 76v-8a10 10 0 0 1 14-8M74 76v-8a10 10 0 0 0-14-8"/></svg>
  <h3>PARTNER PROGRAMME</h3>
  <p>Vantoris offers the White Label Program to Individuals &amp;Institutions that want to establish a brand name in the global markets. As a White Label partner, you will be provided with a Platform with your Brand or Logo</p>
  <span class="btn-outline">CLICK HERE</span>
</div>

<div class="abs card card-demo">
  <svg class="ico" width="76" height="66" viewBox="0 0 76 66" fill="none" stroke="#2d3269" stroke-width="2.5"><rect x="3" y="3" width="70" height="46" rx="2"/><line x1="3" y1="40" x2="73" y2="40"/><line x1="38" y1="49" x2="38" y2="60"/><line x1="24" y1="61" x2="52" y2="61"/></svg>
  <h3>DEMO ACCOUNT</h3>
  <p>You can now practice trading using a demo account with live market rates. We believe that as a client, your understanding of the markets and our services is important before you start actual live trading.</p>
  <span class="btn-outline">CLICK HERE</span>
</div>

<section class="abs callback">
  <h2>REQUEST CALL BACK</h2>
  <div class="field" style="left:199px;top:172px"><label>FIRST NAME</label><div class="input"></div></div>
  <div class="field" style="left:625px;top:172px"><label>CITY</label><div class="input"></div></div>
  <div class="field" style="left:199px;top:263px"><label>PHONE</label><div class="input"></div></div>
  <div class="field" style="left:625px;top:263px"><label>EMAIL ADDRESS</label><div class="input"></div></div>
  <div class="btn-send">SEND</div>
</section>

<section class="abs brands">
  <div class="brand" style="left:170px"><span class="dot"></span>Vexa FX</div>
  <div class="brand" style="left:318px"><span class="dot" style="background:#2f4aa0"></span>Helix Systems</div>
  <div class="brand" style="left:468px"><span class="sq"></span>App Market</div>
  <div class="brand" style="left:652px"><span class="dot" style="background:#4f8a3a"></span>TradeDesk 4</div>
  <div class="brand" style="left:870px"><span class="sq" style="background:#111"></span>App Shelf</div>
</section>

<footer class="abs footer">
  <div class="fcol" style="left:123px"><h4>ABOUT</h4><ul><li>OUR REGULATOR</li><li>COMPLIANCE</li><li>AUDITOR</li><li>GLOBAL NETWORK</li></ul></div>
  <div class="fcol" style="left:321px"><h4>PRODUCTS</h4><ul><li>CFDS</li><li>FOREX</li><li>FUTURES</li><li>STOCKS</li><li>BONDS</li><li>OPTIONS</li></ul></div>
  <div class="fcol" style="left:491px"><h4>PLATFORMS</h4><ul><li>KORA PRO</li><li>KORA TRADER</li><li>DEMO</li><li>SYSTEM MANUAL</li></ul></div>
  <div class="fcol" style="left:697px"><h4>TRADING INFO</h4><ul><li>PRODUCT GUIDE</li><li>CONTRACT SPECIFICATIONS</li><li>MARGINS AND SPREADS</li><li>CONTRACT CALENDER</li><li>CODE OF CONDUCT</li></ul></div>
  <div class="fcol" style="left:925px"><h4>FOLLOW US</h4><div class="social"><span></span><span></span><span></span><span></span></div></div>
</footer>
<div class="abs bottom-bar">© 2018 Company Name. All right reserved</div>

</body>
</html>
```